Business Card for a Dental Office

The design should communicate integrity, quality and reliability. We also want the card look elegant, simple, but still stand out, different from the traditional-dental-office business card.

Industry/Entity Type

Business

```html
<!DOCTYPE html>
<html lang="en">
<head>
<meta charset="utf-8">
<title>Marlow Dental Centre – Business Card</title>
<link href="https://fonts.googleapis.com/css2?family=Lato:wght@400;700&display=swap" rel="stylesheet">
<style>
  :root {
    --canvas: #e9e7e6;
    --frost: #f4f1f0;
    --frost-edge: #e6e1df;
    --ink: #161616;
    --gold: #c9a81c;
    --gold-deep: #c2a31a;
    --gold-bright: #f6ee2a;
    --paper: #ffffff;
    --faint: #b9b4b1;
  }
  * { box-sizing: border-box; margin: 0; padding: 0; }
  html, body { width: 1200px; height: 900px; overflow: hidden; }
  body {
    background: var(--canvas);
    font-family: "Lato", Arial, sans-serif;
    color: var(--ink);
    position: relative;
  }
  .card {
    position: absolute;
    background: var(--frost);
    box-shadow: 0 2px 10px rgba(0,0,0,0.12);
    overflow: hidden;
  }

  /* Front */
  .card-front { left: 78px; top: 34px; width: 588px; height: 363px; }
  .brand {
    position: absolute; left: 110px; top: 34px;
    display: flex; align-items: center; gap: 14px;
  }
  .brand-mark { width: 58px; height: 58px; background: var(--ink); }
  .brand-text { display: flex; flex-direction: column; }
  .brand-name {
    font-weight: 700; font-size: 27px; letter-spacing: 0.2px;
    color: var(--ink); line-height: 1.1;
  }
  .brand-tagline {
    font-size: 14px; color: var(--gold); letter-spacing: 0.6px;
    text-transform: uppercase; margin-top: 2px;
  }
  .contact-band {
    position: absolute; left: 0; top: 162px; width: 100%; height: 181px;
    background: linear-gradient(to bottom, var(--gold-deep) 0%, #e6d824 25%, var(--gold-bright) 55%, #ede423 80%, var(--gold-deep) 100%);
    text-align: center;
  }
  .person-name { font-weight: 700; font-size: 22px; margin-top: 12px; line-height: 1.1; }
  .person-role { font-size: 15px; margin-top: 2px; }
  .contact-list { list-style: none; margin-top: 22px; font-size: 16px; line-height: 24px; }
  .contact-list svg { width: 13px; height: 11px; vertical-align: -1px; margin-right: 3px; fill: var(--ink); }
  .address { font-size: 16px; margin-top: 16px; }

  /* Back */
  .card-back { left: 388px; top: 505px; width: 566px; height: 352px; }
  .back-mark {
    position: absolute; top: 70px; width: 100%; text-align: center;
    font-weight: 700; font-size: 27px; color: var(--faint); opacity: 0.7;
  }
  .appointment {
    position: absolute; left: 0; top: 153px; width: 100%; height: 175px;
    background: var(--paper);
  }
  .appointment-title {
    text-align: center; font-weight: 700; font-size: 22px;
    color: var(--gold); margin-top: 18px;
  }
  .appointment-fields { list-style: none; margin: 16px 0 0 73px; width: 402px; }
  .field {
    display: flex; align-items: flex-end; gap: 6px;
    font-weight: 700; font-size: 14px; height: 41px; padding-bottom: 5px;
  }
  .field:first-child { height: 26px; }
  .dots { flex: 1; border-bottom: 2px dotted var(--ink); margin-bottom: 4px; }
</style>
</head>
<body>
  <section class="card card-front">
    <div class="brand">
      <div class="brand-mark"></div>
      <div class="brand-text">
        <span class="brand-name">MARLOW DENTAL CENTRE</span>
        <span class="brand-tagline">Your smile is your gift to others</span>
      </div>
    </div>
    <div class="contact-band">
      <h1 class="person-name">ALAN REYES</h1>
      <p class="person-role">Managing Direcator</p>
      <ul class="contact-list">
        <li><svg viewBox="0 0 13 11"><path d="M1 3c2-3 9-3 11 0l-1 2-2-1V3C7 2 6 2 4 3v1L2 5z M3 6h7l1 4H2z"/></svg>555-014-2290</li>
        <li><svg viewBox="0 0 13 11"><path d="M0 1h13v9H0z M1 2l5.5 4L12 2z" fill-rule="evenodd"/></svg>hello@marlowdental.com</li>
      </ul>
      <p class="address">1234, Address Goes Here Country Name, 123456</p>
    </div>
  </section>

  <section class="card card-back">
    <div class="back-mark">MARLOW DENTAL CENTRE</div>
    <div class="appointment">
      <h2 class="appointment-title">Your Next Appointment is</h2>
      <ul class="appointment-fields">
        <li class="field">Name :<span class="dots"></span></li>
        <li class="field">Date :<span class="dots"></span></li>
        <li class="field">Time :<span class="dots"></span>AM<span class="dots"></span>PM</li>
      </ul>
    </div>
  </section>
</body>
</html>
```